Ward Compass Business Card Design*

We need a business card design for our company Ward Compass. Our company is specialized in providing online consulting services regarding medical institutions, hospitals and doctors. We work with patients worldwide looking to choose between healthcare providers. We have a website you may use as a reference, where we list doctors and clinics worldwide. So we target Medical providers as well as patients worldwide.
Target Market(s)
Medical Providers and patients around the world
Industry/Entity Type
Medical
Contact Information for Business Card
Salwa Kettani
CEO
+90 612 348 2175
info@wardcompass.example
www.wardcompass.example
14 Annakhil 7 H.R.B. Rabat, Morocco
Requirements
Must have
- Company logo/name on one full side, personal info and smaller logo and company name on the other side.
Nice to have
- Smart and elegant design

```html
<!DOCTYPE html>
<html lang="en">
<head>
<meta charset="utf-8">
<title>Ward Compass — Business Card</title>
<link href="https://fonts.googleapis.com/css2?family=Montserrat:wght@400;600;700&display=swap" rel="stylesheet">
<style>
  :root {
    --stage: #2b2b2d;
    --navy: #0f2f6b;
    --navy-deep: #0c2a5e;
    --paper: #f2f3f5;
    --ink: #12306a;
    --white: #ffffff;
    --mist: #c9d3e6;
  }
  * { box-sizing: border-box; margin: 0; padding: 0; }
  html, body { width: 1200px; height: 997px; overflow: hidden; }
  body {
    background: var(--stage);
    font-family: "Montserrat", Arial, sans-serif;
    position: relative;
  }
  .card {
    position: absolute;
    width: 560px;
    height: 320px;
    border-radius: 22px;
    overflow: hidden;
    box-shadow: 0 18px 40px rgba(0,0,0,.45);
  }
  .card--back {
    left: 110px; top: 110px;
    background: var(--navy);
    display: flex; align-items: center; justify-content: center;
  }
  .card--front {
    left: 530px; top: 540px;
    background: var(--paper);
  }
  .brand { display: flex; align-items: center; gap: 16px; }
  .brand__dot { width: 34px; height: 34px; border-radius: 50%; }
  .brand__name {
    font-weight: 600;
    letter-spacing: 2px;
    text-transform: uppercase;
  }
  .card--back .brand__dot { background: var(--white); }
  .card--back .brand__name { color: var(--white); font-size: 34px; }

  .front__brand {
    position: absolute; left: 48px; top: 0; bottom: 0;
    display: flex; align-items: center;
  }
  .card--front .brand { gap: 12px; }
  .card--front .brand__dot { background: var(--ink); width: 26px; height: 26px; }
  .card--front .brand__name { color: var(--ink); font-size: 24px; }

  .front__panel {
    position: absolute; right: 0; top: 0; bottom: 0;
    width: 212px;
    background: var(--navy-deep);
    padding: 96px 0 0 26px;
    color: var(--white);
  }
  .front__panel::before {
    content: "";
    position: absolute; left: -10px; top: 104px;
    border-top: 10px solid transparent;
    border-bottom: 10px solid transparent;
    border-right: 10px solid var(--navy-deep);
  }
  .person__name { font-size: 15px; font-weight: 700; letter-spacing: .5px; text-transform: uppercase; }
  .person__role { font-size: 11px; font-weight: 600; margin-top: 3px; color: var(--mist); }
  .contact { list-style: none; margin-top: 26px; }
  .contact li {
    display: flex; align-items: center; gap: 8px;
    font-size: 11px; line-height: 1; margin-bottom: 8px;
  }
  .contact svg { width: 14px; height: 14px; flex: none; }
</style>
</head>
<body>
  <section class="card card--back" aria-label="Card back">
    <div class="brand">
      <span class="brand__dot"></span>
      <span class="brand__name">Ward Compass</span>
    </div>
  </section>

  <section class="card card--front" aria-label="Card front">
    <div class="front__brand">
      <div class="brand">
        <span class="brand__dot"></span>
        <span class="brand__name">Ward Compass</span>
      </div>
    </div>
    <div class="front__panel">
      <p class="person__name">Salwa Kettani</p>
      <p class="person__role">CEO</p>
      <ul class="contact">
        <li>
          <svg viewBox="0 0 14 14"><circle cx="7" cy="7" r="7" fill="#fff"/><path d="M4.5 3.8l1.4-.3.8 1.8-.9.7c.4.9 1.1 1.6 2 2l.7-.9 1.8.8-.3 1.4C7.2 9.5 4.7 7 4.5 3.8z" fill="#0c2a5e"/></svg>
          +90 612 348 2175
        </li>
        <li>
          <svg viewBox="0 0 14 14"><circle cx="7" cy="7" r="7" fill="#fff"/><rect x="3.5" y="4.5" width="7" height="5" fill="none" stroke="#0c2a5e" stroke-width="1"/><path d="M3.5 4.5L7 7.3l3.5-2.8" fill="none" stroke="#0c2a5e" stroke-width="1"/></svg>
          info@wardcompass.example
        </li>
        <li>
          <svg viewBox="0 0 14 14"><circle cx="7" cy="7" r="7" fill="#fff"/><circle cx="7" cy="7" r="3.6" fill="none" stroke="#0c2a5e" stroke-width="1"/><path d="M3.4 7h7.2M7 3.4c-1.6 2-1.6 5.2 0 7.2M7 3.4c1.6 2 1.6 5.2 0 7.2" fill="none" stroke="#0c2a5e" stroke-width=".8"/></svg>
          www.wardcompass.example
        </li>
      </ul>
    </div>
  </section>
</body>
</html>
```